Business Card for Multi-Brand Sportswear Company

We are looking for a business card which represents our company and the multiple brands within it.

The company: Fen Athletics (LTD)
The brands: Fen, TavaPuni, ElmStretch, Grit and Rain

Employees using these cards would be representing Fen Athletics, rather than any of the individual brands. You will see a current design within the uploaded files, to give some inspiration. The actual text of the brands is not necessary, but the logos should be on there is some format.

Our creative minds on this are stretched, so we are looking for someone to make this their own, and show us what a good business card should look like.

We may like to get these printed with spot gloss, so keep that in mind with your designs.

www.fenathletics.co.uk

Industry/Entity Type

Business

Contact Information for Business Card

Leo Pemberton-Hale
Operations Manager
(+44) 1632 960 418
Leo@fenathletics.co.uk
www.fenathletics.co.uk

Font styles to use
Sans Serif
Other font styles liked:
• Eurostile

Colors
ffffff

Requirements
Nice to have
• Dark (black) background

```html
<!DOCTYPE html>
<html lang="en">
<head>
<meta charset="utf-8">
<title>Fen Athletics – Business Card</title>
<link rel="stylesheet" href="https://fonts.googleapis.com/css2?family=Saira:wght@400;500;600&display=swap">
<style>
  :root {
    --backdrop: #e6e6e6;
    --card: #ffffff;
    --ink: #0b0b0b;
    --accent: #ec1c24;
    --paper-text: #ffffff;
    --muted: #8a8a8a;
    --brand-violet: #5a4a63;
  }
  * { box-sizing: border-box; margin: 0; padding: 0; }
  html, body {
    width: 1105px; height: 1200px; overflow: hidden;
    background: var(--backdrop);
    font-family: "Saira", "Helvetica Neue", Arial, sans-serif;
  }
  .canvas { position: relative; width: 1105px; height: 1200px; }
  .card {
    position: absolute; left: 192px; width: 720px; height: 412px;
    background: var(--card); overflow: hidden;
  }
  .card--front { top: 147px; }
  .card--back { top: 602px; }
  .card-shapes { position: absolute; inset: 0; }

  .wordmark {
    position: absolute; display: flex; align-items: center; gap: 10px;
    color: var(--ink); font-weight: 600; white-space: nowrap; letter-spacing: 0.02em;
  }
  .wordmark-square { background: var(--accent); flex: none; }
  .card--front .wordmark { left: 80px; top: 192px; font-size: 34px; }
  .card--front .wordmark-square { width: 16px; height: 16px; }
  .card--back .wordmark { left: 0; right: 0; justify-content: center; top: 140px; font-size: 64px; gap: 18px; }
  .card--back .wordmark-square { width: 28px; height: 28px; }

  .contact { position: absolute; left: 437px; top: 95px; color: var(--paper-text); }
  .contact-name { color: var(--accent); font-size: 25px; font-weight: 600; line-height: 1; letter-spacing: 0.01em; }
  .contact-role { font-size: 19px; margin-top: 12px; line-height: 1; }
  .contact-address { font-size: 19px; line-height: 26px; margin-top: 16px; }
  .contact-lines { list-style: none; margin-top: 12px; }
  .contact-lines li { display: flex; align-items: center; gap: 10px; font-size: 19px; line-height: 28px; }
  .contact-lines svg { width: 16px; height: 16px; flex: none; }

  .brand-row {
    position: absolute; left: 0; right: 0; top: 322px;
    display: flex; justify-content: center; align-items: center; gap: 26px;
    font-size: 20px; font-weight: 500; white-space: nowrap;
  }
  .brand--tava { color: var(--muted); }
  .brand--elm { color: var(--brand-violet); }
  .brand--grit { color: var(--accent); }
  .brand--fen { color: var(--ink); }
</style>
</head>
<body>
<main class="canvas">

  <section class="card card--front" aria-label="Business card front">
    <svg class="card-shapes" viewBox="0 0 720 412" aria-hidden="true">
      <path class="accent-blade" d="M0 72 H92 Q103 72 100 82 L24 300 Q16 322 0 329 Z" fill="#ec1c24"/>
      <path class="contact-panel" d="M432 72 H720 V337 H356 Q342 337 346 325 L418 84 Q422 72 432 72 Z" fill="#0b0b0b"/>
    </svg>

    <div class="wordmark"><span class="wordmark-square"></span>Fen Athletics</div>

    <div class="contact">
      <p class="contact-name">Owen Marsh</p>
      <p class="contact-role">Managing Director</p>
      <p class="contact-address">Lower Croft, Ashby<br>Kelden, KD4 2RT</p>
      <ul class="contact-lines">
        <li>
          <svg viewBox="0 0 16 16" aria-hidden="true"><path d="M3.5 1.5 L6 1 L7.5 4.5 L5.8 5.8 Q7 8.8 10.2 10.2 L11.5 8.5 L15 10 L14.5 12.5 Q13.5 15 11 14.5 Q2 12 1.5 5 Q1 2.5 3.5 1.5 Z" fill="#ec1c24"/></svg>
          +44 (0)1632 960418
        </li>
        <li>
          <svg viewBox="0 0 16 16" aria-hidden="true"><rect x="1" y="3" width="14" height="10" fill="#ec1c24"/><path d="M1 3 L8 9 L15 3" fill="none" stroke="#0b0b0b" stroke-width="1.4"/></svg>
          owen@fenathletics.co.uk
        </li>
        <li>
          <svg viewBox="0 0 16 16" aria-hidden="true"><circle cx="8" cy="8" r="7" fill="#ec1c24"/><path d="M1 8 H15 M8 1 Q4 8 8 15 M8 1 Q12 8 8 15" fill="none" stroke="#0b0b0b" stroke-width="1"/></svg>
          www.fenathletics.co.uk
        </li>
      </ul>
    </div>
  </section>

  <section class="card card--back" aria-label="Business card back">
    <div class="wordmark"><span class="wordmark-square"></span>Fen Athletics</div>
    <div class="brand-row">
      <span class="brand brand--tava">TavaPuni</span>
      <span class="brand brand--elm">ElmStretch</span>
      <span class="brand brand--grit">Grit and Rain</span>
      <span class="brand brand--fen">Fen</span>
    </div>
  </section>

</main>
</body>
</html>
```